KTR Design Business Card

I need to develop a business card for my real estate design and investment company. Something clean, classic and professional with a modern vibe.

Industry/Entity Type

Real Estate

Font styles to use
Serif
Sans Serif

```html
<!DOCTYPE html>
<html lang="en">
<head>
<meta charset="utf-8">
<title>KTR Design Business Card</title>
<link href="https://fonts.googleapis.com/css2?family=Montserrat:wght@300;400;600&display=swap" rel="stylesheet">
<style>
  :root {
    --page: #e4e4e2;
    --card-dark: #3b3b3b;
    --card-dark-deep: #262626;
    --card-light: #ffffff;
    --card-light-shade: #e9e9e9;
    --stripe: #b9b9b9;
    --ink: #2e2e2e;
    --ink-soft: #555555;
    --on-dark: #ffffff;
  }
  html, body {
    margin: 0;
    width: 1200px;
    height: 899px;
    overflow: hidden;
    background: var(--page);
    font-family: "Montserrat", Arial, sans-serif;
  }
  .card {
    position: absolute;
    left: 110px;
    top: 165px;
    width: 980px;
    height: 570px;
    border-radius: 48px;
    overflow: hidden;
    box-shadow: 0 10px 30px rgba(0,0,0,0.18);
  }
  .card-art { position: absolute; inset: 0; }
  .holder {
    position: absolute;
    right: 70px;
    top: 62px;
    text-align: right;
    color: var(--on-dark);
  }
  .holder-name {
    font-weight: 600;
    font-size: 34px;
    letter-spacing: 2px;
    margin: 0;
  }
  .holder-role {
    font-weight: 400;
    font-size: 22px;
    margin: 6px 0 0;
  }
  .brand {
    position: absolute;
    left: 400px;
    top: 200px;
    color: var(--ink);
  }
  .brand-name {
    font-weight: 300;
    font-size: 58px;
    letter-spacing: 4px;
    margin: 0;
    line-height: 1;
  }
  .brand-tagline {
    font-weight: 400;
    font-size: 21px;
    margin: 14px 0 0;
    color: var(--ink-soft);
  }
  .contacts {
    position: absolute;
    left: 52px;
    top: 225px;
    list-style: none;
    margin: 0;
    padding: 0;
    color: var(--ink);
    font-size: 17px;
  }
  .contacts li {
    display: flex;
    align-items: center;
    gap: 12px;
    height: 36px;
  }
  .contacts svg { width: 16px; height: 16px; fill: var(--ink-soft); flex: none; }
  .address {
    position: absolute;
    right: 70px;
    bottom: 70px;
    text-align: right;
    color: var(--ink);
    font-size: 20px;
    line-height: 1.45;
    margin: 0;
    font-style: normal;
  }
</style>
</head>
<body>
<section class="card">
  <svg class="card-art" viewBox="0 0 980 570" preserveAspectRatio="none" aria-hidden="true">
    <defs>
      <linearGradient id="dark-band" x1="0" y1="0" x2="1" y2="1">
        <stop offset="0" stop-color="var(--card-dark-deep)"/>
        <stop offset="1" stop-color="var(--card-dark)"/>
      </linearGradient>
      <linearGradient id="light-face" x1="0" y1="0" x2="1" y2="1">
        <stop offset="0" stop-color="var(--card-light-shade)"/>
        <stop offset="0.6" stop-color="var(--card-light)"/>
      </linearGradient>
    </defs>
    <rect width="980" height="570" fill="url(#dark-band)"/>
    <path d="M0 190 C 220 60 560 110 980 205 L980 570 L0 570 Z" fill="var(--stripe)"/>
    <path d="M0 215 C 230 95 560 135 980 225 L980 570 L0 570 Z" fill="url(#light-face)"/>
  </svg>

  <header class="holder">
    <h1 class="holder-name">DANIEL MERCER</h1>
    <p class="holder-role">Managing Director</p>
  </header>

  <div class="brand">
    <p class="brand-name">KTR Design</p>
    <p class="brand-tagline">Spaces and Investments</p>
  </div>

  <ul class="contacts">
    <li><svg viewBox="0 0 16 16"><path d="M3 1h3l1.5 4-2 1.2a9 9 0 0 0 4.3 4.3L11 8.5l4 1.5v3a2 2 0 0 1-2 2A12 12 0 0 1 1 3a2 2 0 0 1 2-2z"/></svg>012 555 0147</li>
    <li><svg viewBox="0 0 16 16"><path d="M4.5 0h7a1.5 1.5 0 0 1 1.5 1.5v13a1.5 1.5 0 0 1-1.5 1.5h-7A1.5 1.5 0 0 1 3 14.5v-13A1.5 1.5 0 0 1 4.5 0zM5 2v10h6V2zm3 11a1 1 0 1 0 0 2 1 1 0 0 0 0-2z"/></svg>012 555 0148</li>
    <li><svg viewBox="0 0 16 16"><path d="M4 1h6l2 2v3H4zM1 7h14v7H1zm3 2v1h2V9zm4 0v1h2V9zm-4 2v1h2v-1zm4 0v1h2v-1z"/></svg>012 555 0149</li>
    <li><svg viewBox="0 0 16 16"><path d="M1 3h14v10H1zm1.5 1.5v.4L8 9l5.5-4.1v-.4zM2.5 6.8v4.7h11V6.8L8 10.9z"/></svg>hello@ktrdesign.com</li>
    <li><svg viewBox="0 0 16 16"><path d="M8 0a8 8 0 1 0 0 16A8 8 0 0 0 8 0zm0 1.5c1 0 2 1.6 2.4 4H5.6C6 3.1 7 1.5 8 1.5zM1.6 7h2.9a15 15 0 0 0 0 2H1.6a6.5 6.5 0 0 1 0-2zm4 0h4.8a14 14 0 0 1 0 2H5.6a14 14 0 0 1 0-2zm5.9 0h2.9a6.5 6.5 0 0 1 0 2h-2.9a15 15 0 0 0 0-2zM5.6 10.5h4.8c-.4 2.4-1.4 4-2.4 4s-2-1.6-2.4-4z"/></svg>www.ktrdesign.com</li>
  </ul>

  <address class="address">57 Crestview Avenue,<br>Suite 12 Northgate</address>
</section>
</body>
</html>
```